Redesign website for small print company

Vindurgata is a small printing company in Iceland mainly servicing Students, schools, etc. We are also doing all kind of other jobs, like business cards, book printing, brochure printing etc. We are also selling books online.
Our website is: www.vindurgata.is
What we are looking for is:
- Web Design (Uncoded - PSD layout only)
- Mobile friendly design, using our current color scheme: Red, green, yellow and light gray.
- Clean simple design
- Simple, light and easy to use.
- More menu Items/drop down
Industry/Entity Type
Digital Printing
Number of Pages Required
5+ page
Requirements
Must have
- Easy navigation
- Designed for mobile
- Current color scheme (see logo)
Nice to have
- Icon based products

```html
<!DOCTYPE html>
<html lang="is">
<head>
<meta charset="utf-8">
<title>Vindurgata – prentsmiðja</title>
<link href="https://fonts.googleapis.com/css2?family=Anton&family=Oswald:wght@500;700&family=Montserrat:wght@400;500;600;700&display=swap" rel="stylesheet">
<style>
:root{
  --green:#0fa46a;
  --green-dark:#0a8a57;
  --red:#e02a2a;
  --yellow:#f3c21a;
  --ink:#222;
  --muted:#8b8b8b;
  --line:#e2e2e2;
  --light:#f1f1f1;
  --footer:#2a2a2a;
  --footer-text:#b9b9b9;
  --white:#fff;
}
*{margin:0;padding:0;box-sizing:border-box}
html,body{width:1200px;height:2932px;overflow:hidden}
body{position:relative;background:var(--white);font-family:"Montserrat",sans-serif;color:var(--ink)}
.abs{position:absolute}

/* header */
.site-header{position:absolute;left:0;top:0;width:1200px;height:68px;background:var(--white)}
.brand{left:160px;top:14px;display:flex;align-items:center;gap:8px}
.brand-mark{width:26px;height:26px;background:var(--red)}
.brand-name{font-weight:700;font-size:21px;color:var(--ink)}
.main-nav{left:420px;top:27px;display:flex;font-size:11px;font-weight:600;letter-spacing:.3px}
.main-nav a{color:var(--ink);text-decoration:none;position:absolute;white-space:nowrap}
.nav-sep{position:absolute;top:2px;width:1px;height:10px;background:#bbb}
.search-icon{left:888px;top:24px}
.cart-btn{left:920px;top:16px;width:116px;height:39px;border:2px solid var(--green);border-radius:3px;color:var(--green);font-size:11px;font-weight:600;display:flex;align-items:center;justify-content:center}

/* hero */
.hero{position:absolute;left:0;top:68px;width:1200px;height:532px;background:linear-gradient(100deg,#4c3f36 0%,#7a6a5c 35%,#8f7c64 60%,#6b5a3f 100%)}
.hero-photo{position:absolute;inset:0;background:linear-gradient(180deg,rgba(0,0,0,.15),rgba(0,0,0,.35))}
.hero-title{left:160px;top:140px;font-family:"Anton",sans-serif;font-size:50px;line-height:62px;color:var(--white);letter-spacing:.5px}
.hero-sub{left:160px;top:280px;font-size:12.5px;font-weight:600;color:var(--white);text-decoration:underline}
.btn-primary{left:160px;top:346px;width:133px;height:43px;background:var(--white);color:var(--red);font-size:12px;font-weight:600;display:flex;align-items:center;justify-content:center;border-radius:2px}
.btn-ghost{left:305px;top:346px;width:129px;height:43px;border:1px solid var(--white);color:var(--white);font-size:12px;font-weight:500;display:flex;align-items:center;justify-content:center;border-radius:2px}
.sample-frame{border:6px solid var(--white);box-shadow:0 6px 16px rgba(0,0,0,.3)}

/* section titles */
.section-title{position:absolute;left:0;width:1200px;text-align:center;font-family:"Oswald",sans-serif;font-weight:700;font-size:25px;color:var(--ink);letter-spacing:.3px}
.section-title span{border-left:4px solid var(--green);border-right:4px solid var(--green);padding:0 10px}

/* catalog */
.product{position:absolute;width:278px;text-align:center}
.product-image{width:278px;height:250px;border:1px solid var(--line)}
.product-name{margin-top:22px;font-size:13px;font-weight:700;letter-spacing:.5px}
.product-desc{margin-top:12px;font-size:11px;line-height:18px;color:var(--muted);padding:0 12px}
.slider-dots{left:567px;top:1562px;display:flex;gap:6px}
.slider-dots i{display:block;width:18px;height:3px;background:var(--ink)}
.slider-dots i.active{background:var(--red)}
.divider{left:0;top:1626px;width:1200px;height:1px;background:var(--line)}

/* about */
.about-card{left:662px;top:1934px;width:362px;height:327px;background:var(--white);box-shadow:0 4px 20px rgba(0,0,0,.12)}
.about-panel{left:176px;top:1757px;width:543px;height:393px;background:var(--green);border-radius:8px;color:var(--white);text-align:center;padding:62px 28px 0}
.about-panel h3{font-size:21px;line-height:32px;font-weight:700}
.about-panel hr{width:40px;border:0;border-top:2px solid var(--white);margin:18px auto 18px}
.about-panel p{font-size:11.5px;line-height:21px}

/* newsletter */
.newsletter{position:absolute;left:0;top:2340px;width:1200px;height:314px;background:linear-gradient(160deg,#f6f6f6,#e8e8e8 60%,#f3f3f3)}
.newsletter-note{left:0;top:2436px;width:1200px;text-align:center;font-size:12px;color:#555}
.field{top:2486px;height:33px;background:var(--white);font-size:11px;color:#555;padding:0 18px;display:flex;align-items:center}
.signup{left:805px;top:2486px;width:112px;height:33px;background:var(--red);color:var(--white);font-size:12px;font-weight:600;display:flex;align-items:center;justify-content:center}
.connect{left:0;top:2547px;width:1200px;text-align:center;font-size:14px;font-weight:700}
.social{top:2581px;width:28px;height:28px;border:1.5px solid #444;border-radius:50%}

/* footer */
.site-footer{position:absolute;left:0;top:2654px;width:1200px;height:278px;background:var(--footer)}
.footer-head{top:2708px;font-size:13px;font-weight:700;color:var(--white);text-decoration:underline}
.footer-link{font-size:10.5px;color:var(--footer-text);white-space:nowrap}
.footer-rule{left:160px;top:2884px;width:880px;height:1px;background:#444}
.copyright{left:0;top:2900px;width:1200px;text-align:center;font-size:10px;color:var(--footer-text)}
</style>
</head>
<body>

<header class="site-header">
  <div class="abs brand"><span class="brand-mark"></span><span class="brand-name">Vindurgata</span></div>
  <nav class="abs main-nav">
    <svg class="abs" style="left:0;top:-1px" width="14" height="12" viewBox="0 0 14 12"><path d="M7 0 0 6h2v6h4V8h2v4h4V6h2z" fill="#222"/></svg>
    <a style="left:22px">HOME</a>
    <span class="nav-sep" style="left:80px"></span>
    <a style="left:104px">SERVICES</a>
    <span class="nav-sep" style="left:178px"></span>
    <a style="left:201px">JOB SUBMIT</a>
    <span class="nav-sep" style="left:285px"></span>
    <a style="left:309px">ABOUT US</a>
  </nav>
  <svg class="abs search-icon" width="18" height="18" viewBox="0 0 18 18"><circle cx="7.5" cy="7.5" r="5.5" fill="none" stroke="#0fa46a" stroke-width="2.2"/><line x1="11.5" y1="11.5" x2="16" y2="16" stroke="#0fa46a" stroke-width="2.4" stroke-linecap="round"/></svg>
  <div class="abs cart-btn">ADD TO CART</div>
</header>

<section class="hero">
  <div class="hero-photo" role="img" aria-label="Students holding books and notebooks on a university campus"></div>
  <div class="abs sample-frame" role="img" aria-label="Rolled printed posters" style="left:674px;top:53px;width:225px;height:237px;background:linear-gradient(135deg,#f4f4f4,#2b2b2b 55%,#ddd)"></div>
  <div class="abs sample-frame" role="img" aria-label="Printed brochure spread" style="left:762px;top:288px;width:100px;height:156px;background:linear-gradient(160deg,#e8eef4,#8aa4c0)"></div>
  <div class="abs sample-frame" role="img" aria-label="Printed textbook cover" style="left:870px;top:290px;width:195px;height:166px;background:linear-gradient(160deg,#e23b3b 0 30%,#f2f2f2 30%)"></div>
</section>
<div class="abs hero-title">WELCOME TO<br>VINDURGATA</div>
<div class="abs hero-sub">Vindurgata er fyrirtæki staðsett á háskólasvæðinu sem hefur</div>
<div class="abs btn-primary">Get Started</div>
<div class="abs btn-ghost">Contact Us</div>

<h2 class="section-title" style="top:670px"><span>OUR CATALOG</span></h2>

<article class="product" style="left:160px;top:772px">
  <div class="product-image" role="img" aria-label="Bound theses and printed documents" style="background:linear-gradient(150deg,#f7f7f7,#e4e4e4)"></div>
  <div class="product-name">RITGERÐIR</div>
  <div class="product-desc">Vindurgata prentar og bindur inn ritgerðir. Ritgerðir eru ýmist kilju­innbundnar</div>
</article>
<article class="product" style="left:461px;top:772px">
  <div class="product-image" role="img" aria-label="Printed business cards" style="background:linear-gradient(180deg,#cfcfcf,#f1f1f1 60%,#bdbdbd)"></div>
  <div class="product-name">NAFNSPJÖLD</div>
  <div class="product-desc">Nafnspjöld hjá Vindurgata er hægt að prenta í öllum stærðum og gerðum.</div>
</article>
<article class="product" style="left:760px;top:772px">
  <div class="product-image" role="img" aria-label="Printed brochures fanned out" style="background:linear-gradient(150deg,#e9e9e9,#9fb4c8 50%,#c98a4e)"></div>
  <div class="product-name">BÆKLINGAR</div>
  <div class="product-desc">Vindurgata prentar bæklinga í öllum stærðum og gerðum á ýmsar tegundir pappírs.</div>
</article>
<article class="product" style="left:160px;top:1168px">
  <div class="product-image" role="img" aria-label="Printed book covers" style="background:linear-gradient(150deg,#e74b8f,#f3c21a 50%,#3a8fd0)"></div>
  <div class="product-name">BÓKAPRENTUN</div>
  <div class="product-desc">Vindurgata sérhæfir sig í að prenta bækur í litlu upplagi, við höfum frábæran búnað til</div>
</article>
<article class="product" style="left:461px;top:1168px">
  <div class="product-image" role="img" aria-label="Rolled wall posters" style="background:linear-gradient(170deg,#f4f4f4 20%,#1f1f1f 45%,#dcdcdc)"></div>
  <div class="product-name">VEGGSPJÖLD</div>
  <div class="product-desc">Vindurgata prentar veggspjöld í mörgum stærðum, á ýmis konar pappír.</div>
</article>
<article class="product" style="left:760px;top:1168px">
  <div class="product-image" role="img" aria-label="Printed textbook" style="background:linear-gradient(150deg,#f6f6f6,#e0e0e0)"></div>
  <div class="product-name">KENNSLUBÆKUR</div>
  <div class="product-desc">Vindurgata sérhæfir sig í að prenta allar tegundir kennslubóka í litlu upplagi.</div>
</article>
<div class="abs slider-dots"><i></i><i></i><i class="active"></i></div>
<div class="abs divider"></div>

<h2 class="section-title" style="top:1674px"><span>ABOUT US</span></h2>
<div class="abs about-card">
  <div class="abs" role="img" aria-label="Tri-fold brochure illustration" style="left:20px;top:59px;width:321px;height:215px;background:linear-gradient(120deg,#dff0fb,#f7f7f7 45%,#fbe6c6)"></div>
</div>
<div class="abs about-panel">
  <h3>Vindurgata er fyrirtæki staðsett á háskólasvæðinu sem hefur sérhæft sig í að þjónusta skólafólk</h3>
  <hr>
  <p>Vindurgata gefur út greinasöfn og fjölmargar kennslubækur fyrir námskeið, prentar lokaritgerðir fyrir nema, auk þess að vinna við ótalinn fjölda smærri verka fyrir nemendur, kennara og stofnanir. Má þar nefna bæklinga, skýrslur, spurningalista, nafnspjöld, bækur, OCR skönnun og fleira.<br>Vindurgata er umhverfisvottuð prentsmiðja, Grænlaufið er opinbert umhverfismerki Norðurlandanna, sem hefur skapað sér fótfestu hér á landi og er þekkt</p>
</div>

<section class="newsletter"></section>
<h2 class="section-title" style="top:2384px"><span>OUR NEWSLETTER</span></h2>
<div class="abs newsletter-note">By signing up you agree with Terms and Privacy Policy</div>
<div class="abs field" style="left:283px;width:256px">Full Name</div>
<div class="abs field" style="left:549px;width:248px">Email Address</div>
<div class="abs signup">Sign Up</div>
<div class="abs connect">Let's Stay Connected</div>
<span class="abs social" style="left:531px"></span>
<span class="abs social" style="left:566px"></span>
<span class="abs social" style="left:603px"></span>
<span class="abs social" style="left:643px"></span>

<footer class="site-footer"></footer>
<div class="abs footer-head" style="left:160px">Contact Us</div>
<div class="abs footer-head" style="left:494px">Navigation</div>
<div class="abs footer-head" style="left:784px">Quick Links</div>

<svg class="abs" style="left:160px;top:2753px" width="13" height="13" viewBox="0 0 13 13"><path d="M3 1 5 4 3.8 5.4c.8 1.6 2.2 3 3.8 3.8L9 8l3 2-1 2C6 12 1 7 1 2z" fill="#b9b9b9"/></svg>
<div class="abs footer-link" style="left:194px;top:2754px">555 0142</div>
<svg class="abs" style="left:161px;top:2790px" width="11" height="14" viewBox="0 0 11 14"><path d="M5.5 0A5.5 5.5 0 0 0 0 5.5C0 9.5 5.5 14 5.5 14S11 9.5 11 5.5A5.5 5.5 0 0 0 5.5 0zm0 7.6a2 2 0 1 1 0-4 2 2 0 0 1 0 4z" fill="#b9b9b9"/></svg>
<div class="abs footer-link" style="left:194px;top:2784px;line-height:22px">IS12 0300 2600 4411 2233 4455 66<br>SWIFT (BIC) VNDGISRE</div>
<svg class="abs" style="left:160px;top:2834px" width="14" height="10" viewBox="0 0 14 10"><rect width="14" height="10" fill="#b9b9b9"/><path d="M0 0 7 6 14 0" fill="none" stroke="#2a2a2a" stroke-width="1.3"/></svg>
<div class="abs footer-link" style="left:194px;top:2832px">verk@vindurgata.is</div>

<div class="abs footer-link" style="left:494px;top:2754px">Home</div>
<div class="abs footer-link" style="left:494px;top:2778px">Services</div>
<div class="abs footer-link" style="left:494px;top:2802px">Job Submit</div>
<div class="abs footer-link" style="left:494px;top:2826px">About Us</div>
<div class="abs footer-link" style="left:637px;top:2754px">Skil á Verkum</div>
<div class="abs footer-link" style="left:637px;top:2778px">Til Okkar</div>
<div class="abs footer-link" style="left:637px;top:2802px">Contact</div>

<div class="abs footer-link" style="left:784px;top:2754px">View Cart</div>
<div class="abs footer-link" style="left:784px;top:2778px">Search</div>
<div class="abs footer-link" style="left:784px;top:2802px">Site Map</div>
<div class="abs footer-link" style="left:784px;top:2826px">Help</div>
<div class="abs footer-link" style="left:928px;top:2754px">Privacy Policy</div>
<div class="abs footer-link" style="left:928px;top:2778px">Terms and Condition</div>

<div class="abs footer-rule"></div>
<div class="abs copyright">© Copyright 2018 Vindurgata. All Rights Reserved.</div>

</body>
</html>
```